Quorimo Business Card Design Project

We need a business card design for quorimo.example a company based in Berlin, Germany.

?Quorimo is marketplace that enables people all over the world to monetize and exchange their individual knowledge and language skills through interactive video sessions. User are matched by their interests.

On Quorimo everybody can be student or teacher (seller or buyer).

We would love to see designs that use or main color blue and green. The design should communicate what Quorimo enables - see my notice above.

Looking so forward to your designs
Cheers from Berlin,
Lorenz

Target Market(s)

globally

Industry/Entity Type

Teacher

Requirements
Must have
• Lorenz Hubeck
CEO
Quorimo.example

Quorimo e-Services GmbH
Lindenweg 87
10247 Berlin

Fon: +49 30 418 906 25 17
Mobile: 49 172 54 91 37 6
E-Mail: l.hubeck@quorimo.example
Web: www.quorimo.example

```html
<!DOCTYPE html>
<html lang="en">
<head>
<meta charset="utf-8">
<title>Quorimo Business Card</title>
<link rel="stylesheet" href="https://fonts.googleapis.com/css2?family=Saira:wght@300;400;600&display=swap">
<style>
  :root {
    --stage: #e4e5e7;
    --card-white: #ffffff;
    --brand-green: #98c13c;
    --brand-blue: #1ba7e0;
    --logo-grey: #6d6e71;
    --text-light: #ffffff;
  }
  * { margin: 0; padding: 0; box-sizing: border-box; }
  html, body {
    width: 954px; height: 1200px; overflow: hidden;
    background: var(--stage);
    font-family: "Saira", Arial, sans-serif;
  }
  .canvas { position: relative; width: 954px; height: 1200px; }
  .card {
    position: absolute; left: 77px; width: 800px; height: 456px;
    border-radius: 26px; overflow: hidden;
    background: var(--card-white);
    box-shadow: 0 4px 10px rgba(0,0,0,0.25);
  }
  .card--front { top: 89px; }
  .card--back { top: 642px; }
  .card__panel {
    position: absolute; top: 0; right: 0; bottom: 0; left: 404px;
    background: var(--brand-green);
  }
  .card__divider {
    position: absolute; top: 0; bottom: 0; left: 399px; width: 3px;
    background: var(--brand-blue);
  }
  .brand {
    position: absolute; left: 0; width: 399px; top: 0; bottom: 0;
    display: flex; align-items: center; justify-content: center; gap: 16px;
  }
  .brand__mark { width: 44px; height: 44px; background: var(--brand-blue); }
  .brand__name {
    font-size: 70px; font-weight: 400; color: var(--logo-grey);
    letter-spacing: -1px; line-height: 1;
  }
  .contact { position: absolute; left: 456px; top: 0; color: var(--text-light); }
  .contact__name {
    position: absolute; top: 68px; white-space: nowrap;
    font-size: 35px; font-weight: 600; line-height: 1;
  }
  .contact__role { position: absolute; top: 114px; font-size: 18px; font-weight: 300; }
  .contact__address {
    position: absolute; top: 178px; white-space: nowrap;
    font-size: 20px; font-weight: 300; line-height: 25px;
  }
  .contact__lines {
    position: absolute; top: 300px; list-style: none; white-space: nowrap;
    font-size: 20px; font-weight: 300; line-height: 25.5px;
  }
  .contact__lines li { display: flex; align-items: center; gap: 7px; }
  .contact__lines svg { width: 16px; height: 16px; flex: none; }
  .website {
    position: absolute; left: 404px; right: 0; top: 0; bottom: 0;
    display: flex; align-items: center; justify-content: center;
    color: var(--text-light); font-size: 30px; font-weight: 600;
  }
</style>
</head>
<body>
<div class="canvas">

  <section class="card card--front">
    <div class="brand">
      <span class="brand__mark"></span>
      <span class="brand__name">quorimo</span>
    </div>
    <div class="card__divider"></div>
    <div class="card__panel"></div>
    <div class="contact">
      <p class="contact__name">Lorenz Hubeck</p>
      <p class="contact__role">CEO</p>
      <p class="contact__address">Quorimo e-Services GmbH<br>Lindenweg 87<br>10247 Berlin</p>
      <ul class="contact__lines">
        <li>
          <svg viewBox="0 0 16 16" fill="none" stroke="#fff" stroke-width="1.4"><path d="M1.5 6c0-2 3-3.5 6.5-3.5S14.5 4 14.5 6l-2.5 1-1-2H5L4 7z"/><rect x="3.5" y="8" width="9" height="6" rx="1"/></svg>
          +49 30 418 906 25 17
        </li>
        <li>
          <svg viewBox="0 0 16 16" fill="none" stroke="#fff" stroke-width="1.4"><rect x="4.5" y="3" width="7" height="12" rx="1.2"/><rect x="6" y="5" width="4" height="3"/><path d="M6 1v2"/></svg>
          49 172 54 91 37 6
        </li>
        <li>
          <svg viewBox="0 0 16 16" fill="none" stroke="#fff" stroke-width="1.4"><rect x="1.5" y="4" width="13" height="9" rx="1"/><path d="M1.5 4.5 8 9.5l6.5-5"/></svg>
          l.hubeck@quorimo.example
        </li>
        <li>
          <svg viewBox="0 0 16 16" fill="none" stroke="#fff" stroke-width="1.3"><circle cx="8" cy="8" r="6.5"/><ellipse cx="8" cy="8" rx="3" ry="6.5"/><path d="M1.5 8h13"/></svg>
          www.quorimo.example
        </li>
      </ul>
    </div>
  </section>

  <section class="card card--back">
    <div class="brand">
      <span class="brand__mark"></span>
      <span class="brand__name">quorimo</span>
    </div>
    <div class="card__divider"></div>
    <div class="card__panel"></div>
    <p class="website">www.quorimo.example</p>
  </section>

</div>
</body>
</html>
```